Business Card Design for Occupational Medicine Start Up Company

We need to design a professional business card. We are a healthcare company providing occupational medicine services to blue collar industries. We are professional, efficient and high quality service providers.

Target Market(s)

Blue Collar Industry: Shipbuilding, Ports, Trucking Companies; The Executives and Safety Officers for these companies

Industry/Entity Type

Healthcare

Contact Information for Business Card

Logo, Name, Title, Email, Phone

Other font styles liked:
• Please match our Brand Guide

Requirements
Must have
• Our Company Colors and Logo

```html
<!DOCTYPE html>
<html lang="en">
<head>
<meta charset="utf-8">
<title>CrewCare Clinics – Business Card</title>
<link rel="stylesheet" href="https://fonts.googleapis.com/css2?family=Montserrat:wght@300;400;600;700&display=swap">
<style>
  :root {
    --navy: #29337a;
    --sky: #29a9e1;
    --amber: #f2b04e;
    --paper: #ffffff;
    --backdrop: #e6e6e6;
    --ink-soft: #3a3f5c;
  }
  * { box-sizing: border-box; margin: 0; padding: 0; }
  html, body { width: 1018px; height: 1200px; overflow: hidden; }
  body {
    background: var(--backdrop);
    font-family: "Montserrat", sans-serif;
    position: relative;
  }
  .brand-header {
    position: absolute; top: 62px; left: 0; width: 100%;
    text-align: center;
  }
  .brand-name {
    font-weight: 600; font-size: 40px; color: var(--navy);
    letter-spacing: 1px;
  }
  .card {
    position: absolute; left: 119px; width: 780px; height: 446px;
    overflow: hidden; background: var(--paper);
  }
  .card--contact { top: 170px; }
  .card--brand { top: 676px; }

  .accent-band {
    position: absolute;
  }
  .card--contact .accent-band {
    left: 0; top: 0; width: 100%; height: 220px;
    background: linear-gradient(100deg, var(--navy) 0%, var(--navy) 45%, var(--sky) 75%, var(--amber) 100%);
  }
  .card--brand .accent-band {
    top: 0; width: 110px; height: 100%;
  }
  .card--brand .accent-band--left {
    left: 0;
    background: linear-gradient(180deg, var(--amber) 0%, var(--sky) 35%, var(--navy) 60%);
  }
  .card--brand .accent-band--right {
    right: 0;
    background: linear-gradient(0deg, var(--amber) 0%, var(--sky) 35%, var(--navy) 60%);
  }

  .card-brand-name {
    position: absolute; font-weight: 600; font-size: 22px;
  }
  .card--contact .card-brand-name { left: 50px; top: 96px; color: var(--paper); }
  .card--brand .card-brand-name {
    left: 0; width: 100%; top: 205px; text-align: center;
    color: var(--navy); font-size: 30px;
  }

  .holder { position: absolute; left: 92px; top: 292px; }
  .holder-name { font-weight: 700; font-size: 26px; color: var(--navy); letter-spacing: -0.3px; }
  .holder-title { font-weight: 300; font-size: 19px; color: var(--ink-soft); margin-top: 2px; }

  .divider {
    position: absolute; left: 425px; top: 272px; width: 2px; height: 116px;
    background: var(--amber);
  }
  .contact-list {
    position: absolute; left: 452px; top: 272px; list-style: none;
    font-size: 14px; font-weight: 400; line-height: 22px; color: var(--ink-soft);
  }
</style>
</head>
<body>
  <header class="brand-header">
    <span class="brand-name">CrewCare Clinics</span>
  </header>

  <section class="card card--contact">
    <div class="accent-band" role="img" aria-label="Decorative flowing wave band in navy, sky blue and amber"></div>
    <span class="card-brand-name">CrewCare Clinics</span>
    <div class="holder">
      <p class="holder-name">DANIEL R. HOLLIS</p>
      <p class="holder-title">Chief Executive Manager</p>
    </div>
    <div class="divider"></div>
    <ul class="contact-list">
      <li>+1 555-010-2480</li>
      <li>info@crewcareclinics.com</li>
      <li>crewcareclinics.com</li>
      <li>2750 Harbor Lane Norfolk,</li>
      <li>VA 23510</li>
    </ul>
  </section>

  <section class="card card--brand">
    <div class="accent-band accent-band--left" role="img" aria-label="Decorative wave edge in navy, sky blue and amber"></div>
    <div class="accent-band accent-band--right" role="img" aria-label="Decorative wave edge in navy, sky blue and amber"></div>
    <span class="card-brand-name">CrewCare Clinics</span>
  </section>
</body>
</html>
```